Design eines Zertifikats
Ich bin total begeistert. Super Kommunikation, super schnelle Reaktion auf kleine Änderungswünsche, ich bin wirklich rundum zufrieden!! Auch bei weiterführenden Fragen die gar nicht direkt mit dem Design zusammenhingen wurde mir total schnell und sympathisch geholfen, ich kann die Designerin nur wärmstens weiterempfehlen!
Zielgruppe
Ich betreibe einen Onlineshop, in dem ich sogenannte Sterntaufen verkaufe. Ein Kunde bekommt dabei im Zuge seines Kaufes ein Zertifikat ausgestellt mit Daten zu seinem getauften Stern. Es geht hier um das Design eines neuen Zertifikats um möglichst noch mehr Käufer anzusprechen. Es sind bereits 3 Designs vorhanden, das neue sollte sich entsprechend etwas absetzen.
Ich lasse die Zertifikate in einer Druckerei drucken, und bedrucke diese dann selber mit den Daten der Sterntaufe, es muss auf dem Zertifikat also ein heller Bereich vorhanden sein in dem ich drucken kann.
Aufgabenstellung
Das Zertifikat soll A4 sein. Es sollte modern sein und sich wie gesagt möglichst von den bestehenden absetzen, und ein möglichst breites Publikum ansprechen.
Beispiele für Zertifikate der Konkurrenz finden sich unter:
himmelspunkt17.de
nebelverzeichnis.de
lichtpate-bundesweit.de
Das von himmelspunkt17.de gefällt mir persönlich ganz gut, aber lasst euch nicht von den Vorschlägen einschränken.
Bitte nicht zu exzessiv kostenpflichtiges Stockmaterial verwenden, ich mache leider aktuell noch Miese mit dem Shop :-)
Bitte schaut auf meine Webseite um ein Gefühl dafür zu bekommen wie viel Platz für Text vorhanden sein muss.

```html
<!DOCTYPE html>
<html lang="de">
<head>
<meta charset="utf-8">
<title>Sternzertifikat</title>
<link rel="stylesheet" href="https://fonts.googleapis.com/css2?family=Great+Vibes&family=Montserrat:wght@300&display=swap">
<style>
  :root {
    --night-deep: #0d1230;
    --night-blue: #1c2a5e;
    --milky-blue: #3a4f8f;
    --dusk-violet: #5b4a86;
    --dusk-amber: #7a5a3e;
    --paper: #ffffff;
    --ink: #111111;
    --rule: #6b6b6b;
    --seal: #1f2466;
  }
  html, body {
    margin: 0;
    padding: 0;
    overflow: hidden;
    background: #ffffff;
  }
  .certificate {
    position: relative;
    width: 1200px;
    height: 842px;
    overflow: hidden;
    background: var(--night-deep);
  }
  .night-sky {
    position: absolute;
    inset: 0;
    background:
      radial-gradient(ellipse 420px 220px at 420px 150px, rgba(90,115,190,0.45), transparent 70%),
      radial-gradient(ellipse 520px 420px at 1200px 842px, rgba(150,105,70,0.75), transparent 70%),
      radial-gradient(ellipse 500px 500px at 1050px 500px, rgba(105,80,150,0.55), transparent 70%),
      linear-gradient(160deg, var(--night-blue) 0%, var(--milky-blue) 35%, var(--night-blue) 60%, var(--dusk-violet) 85%, var(--dusk-amber) 100%);
  }
  .print-field {
    position: absolute;
    left: 173px;
    top: 159px;
    width: 846px;
    height: 846px;
    border-radius: 50%;
    background: var(--paper);
  }
  .seal {
    position: absolute;
    left: 561px;
    top: 186px;
    width: 64px;
    height: 64px;
  }
  .title {
    position: absolute;
    left: 0;
    width: 1190px;
    top: 258px;
    margin: 0;
    text-align: center;
    font-family: "Great Vibes", cursive;
    font-weight: 400;
    font-size: 84px;
    line-height: 110px;
    color: var(--ink);
  }
  .title-rule {
    position: absolute;
    left: 437px;
    top: 401px;
    width: 313px;
    height: 0;
    border-top: 1px solid var(--rule);
  }
  .statement, .register-line {
    position: absolute;
    left: 0;
    width: 1186px;
    margin: 0;
    text-align: center;
    font-family: "Montserrat", sans-serif;
    font-weight: 300;
    font-size: 24px;
    line-height: 31.7px;
    color: var(--ink);
  }
  .statement { top: 436px; }
  .register-line { top: 722px; }
</style>
</head>
<body>
  <main class="certificate">
    <div class="night-sky" role="img" aria-label="Foto eines Sternenhimmels mit Milchstraße, nach rechts unten in violette und warme Töne übergehend"></div>
    <div class="print-field"></div>

    <svg class="seal" viewBox="0 0 64 64" aria-hidden="true">
      <circle cx="32" cy="32" r="30" fill="var(--seal)"/>
    </svg>

    <h1 class="title">Sternzertifikat</h1>
    <div class="title-rule"></div>

    <p class="statement">
      Der Stern mit den Koordinaten<br>
      xx Koordinaten xx<br>
      wurde am 24.09.2022 in das<br>
      Sternenregister eingetragen.<br>
      Der Stern trägt den Namen
    </p>

    <p class="register-line">Die Registernummer lautet</p>
  </main>
</body>
</html>
```